Business Card Design

I already have a company logo for my company. I have a logo for the manufacturer we represent. I want a professional business card design.

```html
<!DOCTYPE html>
<html lang="en">
<head>
<meta charset="utf-8">
<title>Halden Guard LLC – Business Card</title>
<link href="https://fonts.googleapis.com/css2?family=Open+Sans:wght@400;600;700;800&display=swap" rel="stylesheet">
<style>
  :root {
    --stage: #242424;
    --card: #1f1f22;
    --card-edge: #141416;
    --red: #e31e26;
    --gold: #b8902c;
    --white: #ffffff;
    --soft: #e6e6e6;
    --pattern-dark: #262629;
    --pattern-light: #34343a;
  }
  * { box-sizing: border-box; margin: 0; padding: 0; }
  html, body {
    width: 1200px; height: 780px; overflow: hidden;
    background: var(--stage);
    font-family: "Open Sans", Arial, sans-serif;
  }
  .canvas {
    position: relative; width: 1200px; height: 780px;
    display: flex; align-items: center; justify-content: center; gap: 50px;
  }
  .card {
    position: relative; width: 540px; height: 310px;
    background: var(--card); overflow: hidden;
    box-shadow: 0 18px 40px rgba(0,0,0,.45);
  }

  /* Front */
  .brand {
    position: absolute; top: 62px; left: 0; right: 0;
    display: flex; align-items: center; justify-content: center; gap: 12px;
  }
  .brand-square { width: 30px; height: 30px; background: var(--red); }
  .brand-name {
    font-weight: 800; font-size: 30px; letter-spacing: 1px;
    color: var(--white); text-transform: uppercase;
  }
  .band {
    position: absolute; top: 160px; left: 0; right: 0; height: 96px;
    display: flex;
  }
  .band-identity {
    width: 220px; background: var(--gold);
    padding: 18px 0 0 26px;
  }
  .person-name { font-size: 21px; font-weight: 700; color: var(--white); line-height: 1.2; white-space: nowrap; }
  .person-first { color: var(--red); }
  .person-title { font-size: 13px; color: var(--white); margin-top: 4px; }
  .band-divider {
    width: 46px; background: var(--red);
    display: flex; align-items: center; justify-content: center;
  }
  .band-divider span { width: 26px; height: 26px; background: var(--card); }
  .band-contact {
    flex: 1; background: var(--red);
    padding: 10px 0 0 40px;
    display: flex; flex-direction: column; gap: 3px;
  }
  .contact-line {
    display: flex; align-items: center; gap: 9px;
    color: var(--white); font-size: 15px; font-weight: 600; line-height: 1.45;
  }
  .contact-line svg { width: 14px; height: 14px; flex: none; }
  .address {
    position: absolute; top: 272px; left: 26px;
    color: var(--soft); font-size: 13px;
  }

  /* Back */
  .back-pattern {
    position: absolute; inset: 0;
    background: linear-gradient(135deg, var(--pattern-dark) 0%, var(--pattern-light) 100%);
  }
  .back-brand {
    position: absolute; right: 40px; bottom: 34px;
    display: flex; align-items: center; gap: 6px;
  }
  .back-brand .brand-square { width: 12px; height: 12px; }
  .back-brand .brand-name { font-size: 11px; letter-spacing: .5px; }
</style>
</head>
<body>
<main class="canvas">

  <section class="card card-front" aria-label="Business card front">
    <div class="brand">
      <span class="brand-square"></span>
      <span class="brand-name">Halden Guard</span>
    </div>

    <div class="band">
      <div class="band-identity">
        <p class="person-name"><span class="person-first">Marina</span> Kovalenko</p>
        <p class="person-title">Managing Director</p>
      </div>
      <div class="band-divider"><span></span></div>
      <div class="band-contact">
        <p class="contact-line">
          <svg viewBox="0 0 16 16" aria-hidden="true"><path fill="#fff" d="M3.6 1.5l2.3 2.6-1.3 1.8c.9 2 2.5 3.6 4.5 4.5l1.8-1.3 2.6 2.3-1.4 2.1C7 13.3 2.7 9 1.5 3z"/></svg>
          (555) 214-0386
        </p>
        <p class="contact-line">
          <svg viewBox="0 0 16 16" aria-hidden="true"><rect x="1.5" y="3.5" width="13" height="9" fill="none" stroke="#fff" stroke-width="1.6"/><path d="M1.5 4l6.5 5 6.5-5" fill="none" stroke="#fff" stroke-width="1.6"/></svg>
          hello@haldenguard.com
        </p>
        <p class="contact-line">
          <svg viewBox="0 0 16 16" aria-hidden="true"><circle cx="8" cy="8" r="6.5" fill="none" stroke="#fff" stroke-width="1.5"/><ellipse cx="8" cy="8" rx="2.8" ry="6.5" fill="none" stroke="#fff" stroke-width="1.2"/><path d="M1.5 8h13" stroke="#fff" stroke-width="1.2"/></svg>
          www.haldenguard.com
        </p>
      </div>
    </div>

    <p class="address">418 Bayline Ct #12, Harborview, FL 32901, USA</p>
  </section>

  <section class="card card-back" aria-label="Business card back">
    <div class="back-pattern" role="img" aria-label="Repeating tone-on-tone brand emblem pattern"></div>
    <div class="back-brand">
      <span class="brand-square"></span>
      <span class="brand-name">Halden Guard</span>
    </div>
  </section>

</main>
</body>
</html>
```